Consulting company requires a logo and business card design

I require a logo/business card design for a new company based in Sexsmith Alberta called TallMarsh Integrity Consulting Ltd. I plan to provide the following services: Construction management/inspection for the oil and gas industry, as well as general consulting for Asset Management, fleet management, etc. Have attached a copy of resume for use as guide for

Target Market(s)

Businesses within the oil and gas production, construction and shipping industry

Industry/Entity Type

Oil And Gas

Contact Information for Business Card

Believe should highlight, services offered, safety, quality,

Logo Text

TallMarsh Integrity Consulting (TMIC) ?

Font styles to use
Script

Requirements
Must have
• Open to all options

```html
<!DOCTYPE html>
<html lang="en">
<head>
<meta charset="utf-8">
<title>TallMarsh Integrity Consulting Ltd — Business Card</title>
<link rel="stylesheet" href="https://fonts.googleapis.com/css2?family=Lato:wght@400;700&display=swap">
<style>
  :root {
    --crimson: #c8193f;
    --white: #ffffff;
    --ink: #1e1e1e;
    --grey: #555555;
    --rule: #9a9a9a;
    --backdrop: #ecebe9;
  }
  * { box-sizing: border-box; margin: 0; padding: 0; }
  html, body {
    width: 1200px; height: 900px; overflow: hidden;
    background: var(--backdrop);
    font-family: "Lato", sans-serif;
  }
  .canvas { position: relative; width: 1200px; height: 900px; }

  .card {
    position: absolute;
    border-radius: 16px;
    overflow: hidden;
    box-shadow: 0 6px 18px rgba(0,0,0,0.18);
  }

  /* Front */
  .card--front { left: 78px; top: 35px; width: 587px; height: 363px; background: var(--white); }
  .card--front .band {
    position: absolute; left: 0; top: 27px; width: 100%; height: 98px;
    background: var(--crimson);
  }
  .card--front .brand-dot {
    position: absolute; left: 248px; top: 34px; width: 84px; height: 84px;
    border-radius: 50%; background: var(--white);
  }
  .wordmark {
    position: absolute; left: 0; width: 100%; text-align: center;
    font-weight: 700; line-height: 1;
  }
  .wordmark__name { font-size: 30px; }
  .wordmark__sub {
    display: flex; align-items: center; justify-content: center; gap: 10px;
    font-size: 18px; letter-spacing: 4px; margin-top: 6px;
  }
  .wordmark__sub::before, .wordmark__sub::after {
    content: ""; width: 32px; height: 1px; background: currentColor; opacity: .5;
  }
  .card--front .wordmark { top: 143px; color: var(--crimson); }

  .contact-person {
    position: absolute; right: 312px; top: 236px; text-align: right; color: var(--ink);
  }
  .contact-person__name { font-size: 24px; color: var(--crimson); line-height: 1.1; }
  .contact-person__role { font-size: 16px; margin-top: 3px; }
  .contact-person__address { font-size: 15.5px; line-height: 1.3; margin-top: 13px; }

  .contact-list {
    position: absolute; left: 316px; top: 237px; list-style: none;
    font-size: 16px; color: var(--ink);
  }
  .contact-list li { display: flex; align-items: center; gap: 9px; height: 24.5px; }
  .contact-list svg { width: 12px; height: 12px; fill: var(--crimson); flex: none; }

  /* Back */
  .card--back { left: 390px; top: 507px; width: 565px; height: 348px; background: var(--crimson); }
  .card--back .band {
    position: absolute; left: 0; top: 80px; width: 100%; height: 98px;
    background: var(--white);
  }
  .card--back .brand-dot {
    position: absolute; left: 240px; top: 86px; width: 84px; height: 84px;
    border-radius: 50%; background: var(--crimson);
  }
  .card--back .wordmark { top: 194px; color: var(--white); }
</style>
</head>
<body>
<main class="canvas">

  <section class="card card--front" aria-label="Business card front">
    <div class="band"></div>
    <div class="brand-dot"></div>
    <div class="wordmark">
      <div class="wordmark__name">TallMarsh Integrity</div>
      <div class="wordmark__sub">Consulting Ltd</div>
    </div>

    <div class="contact-person">
      <p class="contact-person__name">Daniel Reeves</p>
      <p class="contact-person__role">Managing Director</p>
      <p class="contact-person__address">12345, Address Goes Here<br>Country Name, 123456</p>
    </div>

    <ul class="contact-list">
      <li>
        <svg viewBox="0 0 24 24" aria-hidden="true"><path d="M6.6 10.8a15.1 15.1 0 0 0 6.6 6.6l2.2-2.2a1 1 0 0 1 1-.25 11.4 11.4 0 0 0 3.6.57 1 1 0 0 1 1 1V20a1 1 0 0 1-1 1A17 17 0 0 1 3 4a1 1 0 0 1 1-1h3.5a1 1 0 0 1 1 1c0 1.25.2 2.45.57 3.57a1 1 0 0 1-.25 1z"/></svg>
        (044)-456-7890
      </li>
      <li>
        <svg viewBox="0 0 24 24" aria-hidden="true"><path d="M7 1h10a2 2 0 0 1 2 2v18a2 2 0 0 1-2 2H7a2 2 0 0 1-2-2V3a2 2 0 0 1 2-2zm0 4v13h10V5zm5 14.5a1.2 1.2 0 1 0 0 2.4 1.2 1.2 0 0 0 0-2.4z"/></svg>
        123-456-7890
      </li>
      <li>
        <svg viewBox="0 0 24 24" aria-hidden="true"><path d="M2 5h20v14H2zm2 2v.4l8 5.2 8-5.2V7zm0 2.8V17h16V9.8l-8 5.2z"/></svg>
        info@youremail.com
      </li>
      <li>
        <svg viewBox="0 0 24 24" aria-hidden="true"><path d="M12 2a10 10 0 1 0 0 20 10 10 0 0 0 0-20zm6.9 6h-3a15.6 15.6 0 0 0-1.4-3.6A8 8 0 0 1 18.9 8zM12 4c.8 1.2 1.5 2.5 1.9 4h-3.8c.4-1.5 1.1-2.8 1.9-4zM4.3 14a8 8 0 0 1 0-4h3.4a16.5 16.5 0 0 0 0 4zm.8 2h3a15.6 15.6 0 0 0 1.4 3.6A8 8 0 0 1 5.1 16zm3-8h-3a8 8 0 0 1 4.4-3.6A15.6 15.6 0 0 0 8.1 8zM12 20c-.8-1.2-1.5-2.5-1.9-4h3.8c-.4 1.5-1.1 2.8-1.9 4zm2.3-6H9.7a14.7 14.7 0 0 1 0-4h4.6a14.7 14.7 0 0 1 0 4zm.2 5.6a15.6 15.6 0 0 0 1.4-3.6h3a8 8 0 0 1-4.4 3.6zm1.8-5.6a16.5 16.5 0 0 0 0-4h3.4a8 8 0 0 1 0 4z"/></svg>
        www.website.com
      </li>
    </ul>
  </section>

  <section class="card card--back" aria-label="Business card back">
    <div class="band"></div>
    <div class="brand-dot"></div>
    <div class="wordmark">
      <div class="wordmark__name">TallMarsh Integrity</div>
      <div class="wordmark__sub">Consulting Ltd</div>
    </div>
  </section>

</main>
</body>
</html>
```